Business Card For Halvenmoor Financial Consulting

Hi, I would like a business card designed. Bold, modern.
Please use the same design as the logo. I have also attached the website design to see the overall theme.
Wordmark Font
Color: Hex: #01AEF7

```html
<!DOCTYPE html>
<html lang="en">
<head>
<meta charset="utf-8">
<title>Halvenmoor Financial Consulting — Business Card</title>
<link href="https://fonts.googleapis.com/css2?family=Arimo:wght@400;700&display=swap" rel="stylesheet">
<style>
  :root {
    --backdrop: #3a3a3a;
    --card: #16222c;
    --accent: #01aef7;
    --accent-soft: #2a9fd8;
    --ink-light: #e9eef2;
    --emboss: #233544;
    --emboss-hi: #4f87b3;
  }
  * { margin: 0; padding: 0; box-sizing: border-box; }
  html, body {
    width: 1200px; height: 801px; overflow: hidden;
    background: var(--backdrop);
    font-family: "Arimo", Arial, sans-serif;
  }
  .stage { position: relative; width: 1200px; height: 801px; }
  .card {
    position: absolute; width: 520px; height: 297px;
    background: var(--card);
    border-bottom: 3px solid var(--accent);
  }
  .card--front { left: 50px; top: 110px; }
  .card--back { left: 630px; top: 394px; }

  .front-brand {
    position: absolute; left: 34px; top: 0; bottom: 0; width: 238px;
    display: flex; align-items: center; gap: 10px;
  }
  .brand-square {
    flex: 0 0 auto; width: 26px; height: 26px;
    border: 3px solid var(--accent);
  }
  .brand-name {
    font-weight: 700; font-size: 19px; line-height: 1.15;
    letter-spacing: 0.5px; color: var(--ink-light); text-transform: uppercase;
  }
  .divider {
    position: absolute; left: 282px; top: 70px; width: 1px; height: 160px;
    background: var(--accent-soft);
  }
  .contact {
    position: absolute; left: 300px; top: 70px; width: 210px;
    color: var(--ink-light); font-size: 11.5px; line-height: 1.45;
  }
  .contact__name {
    font-weight: 700; font-size: 17px; color: var(--accent);
    text-transform: uppercase; letter-spacing: 0.3px;
  }
  .contact__role { margin-bottom: 12px; }
  .contact__address { margin-bottom: 12px; }
  .contact__row { display: flex; align-items: center; gap: 6px; }
  .contact__row svg { width: 10px; height: 10px; flex: 0 0 auto; }

  .back-brand {
    position: absolute; inset: 0;
    display: flex; align-items: center; justify-content: center; gap: 14px;
  }
  .back-brand .brand-square {
    width: 40px; height: 40px; border: 4px solid var(--emboss);
  }
  .back-brand .brand-name {
    font-size: 28px; color: var(--emboss-hi); line-height: 1.1;
  }
</style>
</head>
<body>
<main class="stage">
  <section class="card card--front">
    <div class="front-brand">
      <span class="brand-square"></span>
      <span class="brand-name">Halvenmoor Financial Consulting</span>
    </div>
    <div class="divider"></div>
    <div class="contact">
      <p class="contact__name">Marlo Venstrick</p>
      <p class="contact__role">President</p>
      <p class="contact__address">1180 Harbor Crest Way<br>Seaview CA 92740</p>
      <p class="contact__row">
        <svg viewBox="0 0 10 10"><path d="M2 1l2 2-1 1.5c.6 1.2 1.3 1.9 2.5 2.5L7 6l2 2-1.5 1.5C4 9 1 6 .5 2.5z" fill="var(--accent)"/></svg>
        555-014-2290
      </p>
      <p class="contact__row">
        <svg viewBox="0 0 10 10"><rect x="0.5" y="2" width="9" height="6" fill="var(--accent)"/><path d="M0.5 2l4.5 3.5L9.5 2" stroke="var(--card)" fill="none"/></svg>
        info@HalvenmoorConsulting.com
      </p>
      <p class="contact__row">
        <svg viewBox="0 0 10 10"><circle cx="5" cy="5" r="4.5" fill="var(--accent)"/><path d="M0.5 5h9M5 .5c-2 2.5-2 6.5 0 9M5 .5c2 2.5 2 6.5 0 9" stroke="var(--card)" stroke-width=".7" fill="none"/></svg>
        www.HalvenmoorConsulting.com
      </p>
    </div>
  </section>

  <section class="card card--back">
    <div class="back-brand">
      <span class="brand-square"></span>
      <span class="brand-name">Halvenmoor Financial<br>Consulting</span>
    </div>
  </section>
</main>
</body>
</html>
```